Retail Jewelry Business Card Design Project

We are in need of a new business card design for a retail jewelry store. This store is in the business of fine jewelry including but not specific to bridal jewelry, diamonds, designer jewelry and watches.

This store has been in business for 20 years but continues to strive for a modern professional appeal. The main colors use for this business are a royal blue, white and silver.

Target Market(s)

Target market is ages 18-50

Industry/Entity Type

Jewelry

Requirements
Must have
• Sales Person Name
Sales Person Email Address

Store Address
Store Phone
Website

Standard business card size. No odd shapes or sizes.
Nice to have
• Overall modern feel for card.

We have thought that a design with a nice feature of the logo on the back of the card would be nice but open to ideas.
Should not have
• No specific images of jewelry should be used.

```html
<!DOCTYPE html>
<html lang="en">
<head>
<meta charset="utf-8">
<title>Marlow Reed Fine Jewelry – Business Cards</title>
<link href="https://fonts.googleapis.com/css2?family=Open+Sans:wght@400;600&display=swap" rel="stylesheet">
<style>
  :root {
    --page-bg: #ffffff;
    --card-dark: #121528;
    --card-edge: #0c0e1c;
    --card-glow: #0f2a52;
    --text-light: #f2f2f7;
    --text-soft: #e4e4ee;
    --accent-violet: #7a74c4;
    --accent-tab: #3a34b0;
  }
  * { margin: 0; padding: 0; box-sizing: border-box; }
  html, body {
    width: 1200px;
    height: 1000px;
    overflow: hidden;
    background: var(--page-bg);
    font-family: "Open Sans", sans-serif;
  }
  .canvas { position: relative; width: 1200px; height: 1000px; }

  .card {
    position: absolute;
    left: 285px;
    width: 653px;
    height: 373px;
    border-radius: 24px;
    overflow: hidden;
    background:
      radial-gradient(ellipse 55% 65% at 52% 50%, var(--card-glow) 0%, rgba(15,42,82,0.35) 55%, rgba(18,21,40,0) 100%),
      linear-gradient(180deg, var(--card-dark), var(--card-edge));
    box-shadow: 3px 5px 7px rgba(0,0,0,0.35);
    color: var(--text-light);
  }
  .card--front { top: 102px; }
  .card--back { top: 533px; }

  .brand-name {
    position: absolute;
    text-align: center;
    font-weight: 400;
    color: var(--text-light);
    line-height: 1;
  }
  .brand-name__main { display: block; font-size: 50px; letter-spacing: 1px; }
  .brand-name__sub { display: block; font-size: 19px; letter-spacing: 3px; margin-top: 10px; text-transform: uppercase; }

  .card--front .brand-name { left: 0; width: 653px; top: 132px; }
  .front-web {
    position: absolute;
    left: 0; width: 653px; top: 318px;
    text-align: center;
    font-size: 15px;
    letter-spacing: 1.2px;
    color: var(--text-soft);
  }

  .card--back .brand-name { left: 290px; width: 320px; top: 60px; }
  .card--back .brand-name__main { font-size: 44px; }
  .card--back .brand-name__sub { font-size: 17px; }

  .store-address {
    position: absolute;
    right: 42px; top: 203px;
    text-align: right;
    font-size: 15px;
    line-height: 22px;
    color: var(--text-soft);
  }
  .contact-list {
    position: absolute;
    right: 42px; top: 259px;
    list-style: none;
    font-size: 15px;
    line-height: 22px;
    color: var(--text-soft);
  }
  .contact-list li { display: flex; justify-content: flex-end; align-items: center; gap: 8px; }
  .contact-list svg { width: 17px; height: 14px; fill: var(--accent-violet); }

  .side-tab {
    position: absolute;
    left: 0; top: 268px;
    width: 15px; height: 66px;
    background: var(--accent-tab);
    border-radius: 0 8px 8px 0;
  }
  .staff {
    position: absolute;
    left: 50px; top: 277px;
  }
  .staff__name { font-size: 20px; font-weight: 600; color: var(--accent-violet); line-height: 26px; }
  .staff__role { font-size: 15px; color: var(--text-soft); line-height: 22px; }
</style>
</head>
<body>
<main class="canvas">

  <section class="card card--front" aria-label="Card front">
    <div class="brand-name">
      <span class="brand-name__main">Marlow Reed</span>
      <span class="brand-name__sub">Fine Jewelry</span>
    </div>
    <p class="front-web">www.marlowreedjewelry.com</p>
  </section>

  <section class="card card--back" aria-label="Card back">
    <div class="brand-name">
      <span class="brand-name__main">Marlow Reed</span>
      <span class="brand-name__sub">Fine Jewelry</span>
    </div>

    <address class="store-address" style="font-style:normal">
      2280 Linden Avenue<br>
      Bayport, FL 32999
    </address>

    <ul class="contact-list">
      <li>000.000.0000
        <svg viewBox="0 0 17 14" aria-hidden="true"><path d="M1 5c0-2 3-3.5 7.5-3.5S16 3 16 5l-3 1-1-2H5L4 6 1 5z"/><rect x="3" y="7" width="11" height="6" rx="1"/></svg>
      </li>
      <li>marlow@marlowreedjewelry.com
        <svg viewBox="0 0 17 14" aria-hidden="true"><path d="M1 2h15v10H1z M2 3l6.5 5L15 3" fill="none" stroke="#7a74c4" stroke-width="1.6"/><path d="M1 2h15L8.5 8z"/></svg>
      </li>
      <li>www.marlowreedjewelry.com
        <svg viewBox="0 0 17 14" aria-hidden="true"><g fill="none" stroke="#7a74c4" stroke-width="1.3"><circle cx="8.5" cy="7" r="6"/><ellipse cx="8.5" cy="7" rx="2.6" ry="6"/><path d="M2.5 7h12M3.5 4h10M3.5 10h10"/></g></svg>
      </li>
    </ul>

    <div class="side-tab"></div>
    <div class="staff">
      <p class="staff__name">Marlow Reed Halvorsen</p>
      <p class="staff__role">Owner</p>
    </div>
  </section>

</main>
</body>
</html>
```